BUSINESS CARD FOR GUITAR SCHOOL

I would like to design a business card for my Guitar Music School. The school is called "Pluck & Lantern".

The card should be yellow.

Target Market(s)

18-35 years old

Industry/Entity Type

School

Contact Information for Business Card

I would like to design a business card for my Guitar Music School. The school is called "Pluck & Lantern". The card should be yellow.

Card must be consistent with my website design: www.pluckandlantern.com.sg

Requirements
Must have
• 1) Name of Company
• 2) Company Logo
• 3) Name of Employee
• 4) Position of Employee
• 5) Contact Number
• 6) Address
Nice to have
• Creative Design
• Card must be consistent with my website design: www.pluckandlantern.com.sg
Should not have
• Boring Design

```html
<!DOCTYPE html>
<html lang="en">
<head>
<meta charset="utf-8">
<title>Pluck &amp; Lantern — Business Card</title>
<link rel="stylesheet" href="https://fonts.googleapis.com/css2?family=Open+Sans:wght@400;600;700&family=Poppins:wght@800&display=swap">
<style>
  :root {
    --yellow: #f4c20d;
    --yellow-deep: #e9b000;
    --black: #0e0e0e;
    --ink: #1a1a1a;
    --muted: #6b6b6b;
    --paper: #ffffff;
    --stage: #e9e6e1;
  }
  * { margin: 0; padding: 0; box-sizing: border-box; }
  html, body { width: 1200px; height: 913px; overflow: hidden; }
  body {
    background: var(--stage);
    font-family: "Open Sans", Arial, sans-serif;
    position: relative;
  }
  .card {
    position: absolute;
    width: 520px;
    height: 297px;
    top: 308px;
    border-radius: 3px;
    overflow: hidden;
    box-shadow: 0 6px 18px rgba(0,0,0,0.18);
  }
  /* Front */
  .card-front { left: 60px; background: var(--black); }
  .front-brand {
    position: absolute;
    left: 0; right: 0; top: 112px;
    text-align: center;
  }
  .front-name {
    font-family: "Poppins", Arial, sans-serif;
    font-weight: 800;
    font-size: 44px;
    line-height: 1;
    color: var(--yellow);
    letter-spacing: -1px;
  }
  .front-tagline {
    margin-top: 8px;
    font-size: 13px;
    font-weight: 600;
    color: var(--yellow);
  }
  /* Back */
  .card-back { left: 620px; background: var(--paper); }
  .back-band {
    position: absolute;
    left: 0; top: 0; bottom: 0;
    width: 112px;
    background: linear-gradient(180deg, var(--yellow), var(--yellow-deep));
    border-right: 5px solid var(--black);
  }
  .back-brand { position: absolute; left: 132px; top: 30px; }
  .back-name {
    font-family: "Poppins", Arial, sans-serif;
    font-weight: 800;
    font-size: 22px;
    line-height: 1;
    color: var(--black);
    letter-spacing: -0.5px;
  }
  .back-tagline { margin-top: 4px; font-size: 8px; font-weight: 600; color: var(--ink); }
  .person { position: absolute; right: 24px; top: 30px; text-align: right; }
  .person-name { font-size: 16px; font-weight: 700; color: var(--ink); }
  .person-role { font-size: 10px; color: var(--muted); margin-top: 1px; }
  .contact {
    position: absolute;
    left: 132px; bottom: 26px;
    font-size: 11.5px;
    line-height: 1.55;
    color: var(--ink);
    list-style: none;
  }
  .contact li { display: flex; align-items: center; gap: 8px; }
  .contact .plain { padding-left: 0; }
  .contact svg { width: 12px; height: 12px; flex: none; fill: var(--yellow-deep); }
</style>
</head>
<body>
  <section class="card card-front" aria-label="Card front">
    <div class="front-brand">
      <div class="front-name">Pluck &amp; Lantern</div>
      <div class="front-tagline">Taking Worship to the Next Level</div>
    </div>
  </section>

  <section class="card card-back" aria-label="Card back">
    <div class="back-band"></div>
    <div class="back-brand">
      <div class="back-name">Pluck &amp; Lantern</div>
      <div class="back-tagline">Taking Worship to the Next Level</div>
    </div>
    <div class="person">
      <div class="person-name">Your Long Name</div>
      <div class="person-role">Managing Director</div>
    </div>
    <ul class="contact">
      <li class="plain">22 Kembangan Lane Harbour Building</li>
      <li class="plain">C #05-03 Singapore 418270</li>
      <li>
        <svg viewBox="0 0 12 12" aria-hidden="true"><path d="M2.5 1h2l1 2.6-1.3.9a6 6 0 0 0 3.3 3.3l.9-1.3L11 7.5v2c0 .8-.7 1.5-1.5 1.5A8.5 8.5 0 0 1 1 2.5C1 1.7 1.7 1 2.5 1z"/></svg>
        +65 91234567
      </li>
      <li>
        <svg viewBox="0 0 12 12" aria-hidden="true"><path d="M1 3h10v6.5H1z M1 3l5 3.6L11 3" stroke="#fff" stroke-width="0.8"/></svg>
        yourname@pluckandlantern.com.sg
      </li>
      <li>
        <svg viewBox="0 0 12 12" aria-hidden="true"><circle cx="6" cy="6" r="5"/><path d="M1 6h10M6 1c2 2.5 2 7.5 0 10M6 1c-2 2.5-2 7.5 0 10" stroke="#fff" stroke-width="0.7" fill="none"/></svg>
        www.pluckandlantern.com.sg
      </li>
    </ul>
  </section>
</body>
</html>
```